Pellowar

We need logo and wesbsite for a software development company based out of Hyderabad, India focused on startups and mid sized companies focused on build a new software products in USA and Europe countires.

Target Market(s)

startup and midsized companies in teh USA and Europe for software product development.

Industry/Entity Type

software development

Coding

Coded - Design and coding required

Number of Pages Required

5+ page

Requirements
Must have
• latest design concepts and very elegant
Nice to have
• each page should have images that reflects the content
Should not have
• too many colors

```html
<!DOCTYPE html>
<html lang="en">
<head>
<meta charset="utf-8">
<title>Pellowar</title>
<link href="https://fonts.googleapis.com/css2?family=Catamaran:wght@300;400&family=Lato:wght@400;700&family=Nunito:wght@700;800;900&display=swap" rel="stylesheet">
<style>
:root{
  --violet:#9b6ff0;
  --blue:#43b2fb;
  --grad:linear-gradient(90deg,#a36cf0,#46b3fb);
  --ink:#1b1b22;
  --text:#4a4a55;
  --muted:#666;
  --soft:#f6f6f8;
  --white:#fff;
  --foot-a:#2a1a46;
  --foot-b:#112040;
  --base:#0f1229;
}
*{margin:0;padding:0;box-sizing:border-box}
html,body{width:1200px;height:2964px;overflow:hidden}
body{position:relative;background:var(--white);font-family:"Lato",sans-serif;color:var(--text)}
.abs{position:absolute}
.brand{display:flex;align-items:center;gap:10px;font-family:"Catamaran",sans-serif;font-weight:400;font-size:29px;color:var(--ink)}
.brand-dot{width:34px;height:34px;border-radius:50%;border:3px solid var(--violet)}
.nav{position:absolute;top:0;left:0;width:1200px;height:68px;background:var(--white)}
.nav .brand{position:absolute;left:100px;top:15px}
.nav-links{position:absolute;right:99px;top:30px;display:flex;gap:24px;font-size:12.5px;color:#333;list-style:none}
.nav-links .active{color:var(--violet);border-bottom:1px solid var(--violet);padding-bottom:4px}
.hero{position:absolute;top:68px;left:0;width:1200px;height:393px;overflow:hidden;background:linear-gradient(100deg,#a56ef0 0%,#8a83f1 45%,#45b4fb 100%)}
.bubble{position:absolute;border-radius:50%;background:rgba(150,110,240,.35)}
.hero h1{position:absolute;left:99px;top:92px;font-family:"Nunito",sans-serif;font-weight:900;font-size:37px;line-height:45px;color:var(--white)}
.hero p{position:absolute;left:101px;top:194px;width:430px;font-size:12.5px;line-height:17px;color:var(--white)}
.btn-light{position:absolute;left:99px;top:268px;width:139px;height:44px;border-radius:22px;background:var(--white);color:#333;font-size:12.5px;display:flex;align-items:center;justify-content:center}
.hero-photo{position:absolute;left:704px;top:47px;width:300px;height:300px;border-radius:50%;border:5px solid var(--white);background:radial-gradient(circle at 60% 55%,#e8e8e6,#bfc0c0 70%,#6b6f75);box-shadow:-10px -8px 0 #8b5fe6}
.dots{position:absolute;left:585px;top:347px;display:flex;gap:7px}
.dots span{width:10px;height:10px;border-radius:50%;background:var(--white)}
.dots span:first-child{background:rgba(255,255,255,.5)}
.section-head{position:absolute;left:0;width:1200px;text-align:center}
.section-head .kicker{font-family:"Catamaran",sans-serif;font-size:19px;color:#555}
.section-head h2{font-family:"Catamaran",sans-serif;font-weight:400;color:var(--ink);line-height:1}
.section-head .rule{width:134px;height:3px;margin:0 auto;background:var(--grad)}
.services{position:absolute;top:461px;left:0;width:1200px;height:969px;background:var(--soft)}
.intro{position:absolute;top:186px;left:360px;width:480px;text-align:center;font-size:14.5px;line-height:17.5px;color:#333}
.card{position:absolute;width:308px;height:274px;background:var(--white);border:1px solid #ececf0;text-align:center}
.card .icon{position:absolute;left:104px;top:37px}
.card h3{position:absolute;top:148px;width:100%;font-family:"Nunito",sans-serif;font-weight:800;font-size:24px;color:var(--ink)}
.card p{position:absolute;top:188px;left:24px;width:260px;font-size:12.5px;line-height:19px;color:#555}
.blog-band{position:absolute;top:1731px;left:0;width:1200px;height:390px;background:var(--soft)}
.post{position:absolute;top:1664px;width:308px;height:367px;background:var(--white);box-shadow:0 0 4px rgba(0,0,0,.08)}
.post .photo{position:absolute;left:9px;top:10px;width:288px;height:159px}
.post .accent{position:absolute;right:0;top:80px;width:0;height:0;border-left:90px solid transparent;border-bottom:97px solid var(--blue);opacity:.95}
.post .accent2{position:absolute;right:10px;top:169px;width:80px;height:8px;background:linear-gradient(90deg,#a36cf0,#6b8cf5);clip-path:polygon(10% 0,100% 0,100% 100%,0 100%)}
.post h4{position:absolute;left:16px;top:184px;font-family:"Catamaran",sans-serif;font-weight:400;font-size:21px;color:var(--ink)}
.post .mini{position:absolute;left:17px;top:215px;width:26px;height:2px;background:var(--grad)}
.post p{position:absolute;left:17px;top:232px;width:240px;font-size:12.5px;line-height:16.5px;color:#555}
.read{position:absolute;left:16px;top:300px;width:116px;height:34px;border-radius:17px;background:var(--grad);color:var(--white);font-size:12.5px;padding:9px 0 0 16px}
.read svg{position:absolute;right:3px;top:3px}
.cta{position:absolute;top:2121px;left:0;width:1200px;height:431px;background:radial-gradient(ellipse at 70% 40%,#4a4339,#2b2a2d 60%,#1f1f24);text-align:center;color:var(--white)}
.cta .tag{position:absolute;top:94px;width:100%;font-size:19px}
.cta h2{position:absolute;top:122px;width:100%;font-family:"Catamaran",sans-serif;font-weight:400;font-size:50px}
.cta p{position:absolute;top:193px;left:316px;width:568px;font-size:14.5px;line-height:23.5px}
.btn-grad{position:absolute;left:502px;top:311px;width:196px;height:43px;border-radius:22px;background:var(--grad);color:var(--white);font-size:14px;padding-top:12px}
.footer{position:absolute;top:2552px;left:0;width:1200px;height:297px;background:linear-gradient(100deg,var(--foot-a),var(--foot-b));color:var(--white)}
.footer h5{position:absolute;top:40px;font-family:"Catamaran",sans-serif;font-weight:400;font-size:25px}
.footer .mini{position:absolute;top:78px;width:48px;height:2px;background:var(--grad)}
.footer .about{position:absolute;left:99px;top:101px;width:262px;font-size:12px;line-height:19px}
.links{position:absolute;left:443px;top:101px;list-style:none;font-size:12.5px;line-height:23.5px}
.links li::before{content:"» ";color:#7d8cf5}
.contact{position:absolute;left:751px;top:104px;font-size:14px;line-height:20px}
.contact div{position:relative;padding-left:20px;margin-bottom:9px}
.contact b{display:block}
.contact svg{position:absolute;left:0;top:2px}
.base{position:absolute;top:2849px;left:0;width:1200px;height:115px;background:var(--base);color:var(--white)}
.base .brand{position:absolute;left:99px;top:40px;color:var(--white)}
.base .copy{position:absolute;left:0;width:1200px;top:58px;text-align:center;font-size:11px;letter-spacing:4.5px}
.social{position:absolute;left:1000px;top:54px;display:flex;gap:8px}
.social span{width:19px;height:19px;border-radius:50%;border:1.5px solid var(--white)}
</style>
</head>
<body>

<header class="nav">
  <div class="brand"><span class="brand-dot"></span>Pellowar</div>
  <ul class="nav-links">
    <li class="active">Home</li><li>About Us</li><li>Our Product</li><li>Our Team</li><li>Case Study</li><li>Contact Us</li>
  </ul>
</header>

<section class="hero">
  <span class="bubble" style="left:-40px;top:-60px;width:320px;height:320px"></span>
  <span class="bubble" style="left:330px;top:-40px;width:310px;height:310px"></span>
  <span class="bubble" style="left:100px;top:220px;width:280px;height:280px;background:rgba(140,120,240,.3)"></span>
  <span class="bubble" style="left:960px;top:20px;width:150px;height:150px;background:rgba(110,140,245,.35)"></span>
  <span class="bubble" style="left:1040px;top:245px;width:120px;height:120px;background:rgba(110,130,245,.4)"></span>
  <h1>Software Development<br>For Your Business Services</h1>
  <p>Lorem ipsum dolor sit amet, consectetur adipiscing elit, sed do eiusmod tempor incididunt ut labore et dolore magna aliqua, magna aliqua. ipsum is simply dummy text of the printing.</p>
  <div class="btn-light">Know More</div>
  <div class="hero-photo" role="img" aria-label="Laptop, glasses and mouse on a marble desk"></div>
  <div class="dots"><span></span><span></span><span></span><span></span><span></span></div>
</section>

<section class="services">
  <div class="section-head" style="top:58px">
    <div class="kicker">Lorem ipsum dolor sit amet</div>
    <h2 style="font-size:56px;margin:6px 0 10px">Dolor Amet</h2>
    <div class="rule"></div>
  </div>
  <p class="intro">Lorem ipsum dolor sit amet, consectetur adipiscing elit, sed do eiusmod tempor incididunt ut labore et dolore magna aliqua, magna aliqua. ipsum is simply dummy text of the printing.</p>
</section>

<!-- service icons -->
<svg width="0" height="0" style="position:absolute">
  <defs>
    <linearGradient id="ring" x1="0" y1="0" x2="1" y2="1"><stop offset="0" stop-color="#43b2fb"/><stop offset="1" stop-color="#9b6ff0"/></linearGradient>
    <symbol id="ringbase" viewBox="0 0 100 100">
      <circle cx="50" cy="50" r="42" fill="#f4f1fc"/>
      <path d="M56 8 A42 42 0 1 0 92 56" fill="none" stroke="url(#ring)" stroke-width="6"/>
    </symbol>
  </defs>
</svg>

<div class="card" style="left:98px;top:762px">
  <svg class="icon" width="100" height="100"><use href="#ringbase"/><g stroke="#6b7ff0" stroke-width="2.5" fill="#7e6ff0"><line x1="38" y1="58" x2="46" y2="44"/><line x1="46" y1="44" x2="60" y2="60"/><line x1="46" y1="44" x2="54" y2="38"/><circle cx="38" cy="58" r="4"/><circle cx="46" cy="44" r="4"/><circle cx="60" cy="60" r="4"/><circle cx="54" cy="38" r="3"/></g></svg>
  <h3>IT Solution</h3>
  <p>Lorem ipsum dolor sit amet, consectetur adip-isicing elit, sed do eiusmod tempor incididunt laboret dolore business.</p>
</div>
<div class="card" style="left:441px;top:762px">
  <svg class="icon" width="100" height="100"><use href="#ringbase"/><rect x="32" y="36" width="38" height="25" rx="2" fill="#6b8cf5"/><path d="M34 59 L68 38 L68 59Z" fill="#a56ef0"/><rect x="46" y="62" width="10" height="4" fill="#6b8cf5"/></svg>
  <h3>Web Development</h3>
  <p>Lorem ipsum dolor sit amet, consectetur adip-isicing elit, sed do eiusmod tempor incididunt laboret dolore business.</p>
</div>
<div class="card" style="left:790px;top:762px">
  <svg class="icon" width="100" height="100"><use href="#ringbase"/><g fill="none" stroke="#6b7ff0" stroke-width="2"><rect x="44" y="30" width="12" height="9"/><rect x="33" y="52" width="12" height="9"/><rect x="55" y="52" width="12" height="9"/><path d="M50 39 V46 M39 46 H61 M39 46 V52 M61 46 V52 M36 64 H42 M58 64 H64"/></g></svg>
  <h3>Networking Services</h3>
  <p>Lorem ipsum dolor sit amet, consectetur adip-isicing elit, sed do eiusmod tempor incididunt laboret dolore business.</p>
</div>
<div class="card" style="left:98px;top:1071px">
  <svg class="icon" width="100" height="100"><use href="#ringbase"/><g stroke="#6b7ff0" stroke-width="2.5" fill="#7e6ff0"><line x1="38" y1="58" x2="46" y2="44"/><line x1="46" y1="44" x2="60" y2="60"/><line x1="46" y1="44" x2="54" y2="38"/><circle cx="38" cy="58" r="4"/><circle cx="46" cy="44" r="4"/><circle cx="60" cy="60" r="4"/><circle cx="54" cy="38" r="3"/></g></svg>
  <h3>IT Solution</h3>
  <p>Lorem ipsum dolor sit amet, consectetur adip-isicing elit, sed do eiusmod tempor incididunt laboret dolore business.</p>
</div>
<div class="card" style="left:441px;top:1071px">
  <svg class="icon" width="100" height="100"><use href="#ringbase"/><rect x="32" y="36" width="38" height="25" rx="2" fill="#6b8cf5"/><path d="M34 59 L68 38 L68 59Z" fill="#a56ef0"/><rect x="46" y="62" width="10" height="4" fill="#6b8cf5"/></svg>
  <h3>Web Development</h3>
  <p>Lorem ipsum dolor sit amet, consectetur adip-isicing elit, sed do eiusmod tempor incididunt laboret dolore business.</p>
</div>
<div class="card" style="left:790px;top:1071px">
  <svg class="icon" width="100" height="100"><use href="#ringbase"/><g fill="none" stroke="#6b7ff0" stroke-width="2"><rect x="44" y="30" width="12" height="9"/><rect x="33" y="52" width="12" height="9"/><rect x="55" y="52" width="12" height="9"/><path d="M50 39 V46 M39 46 H61 M39 46 V52 M61 46 V52 M36 64 H42 M58 64 H64"/></g></svg>
  <h3>Networking Services</h3>
  <p>Lorem ipsum dolor sit amet, consectetur adip-isicing elit, sed do eiusmod tempor incididunt laboret dolore business.</p>
</div>

<div class="section-head" style="top:1502px">
  <div class="kicker">Lorem ipsum dolor sit amet</div>
  <h2 style="font-size:63px;margin:6px 0 20px">Lorem Ipsum</h2>
  <div class="rule"></div>
</div>

<div class="blog-band"></div>

<article class="post" style="left:98px">
  <div class="accent"></div><div class="accent2"></div>
  <div class="photo" role="img" aria-label="Person typing on a laptop at a wooden desk" style="background:linear-gradient(135deg,#c9b8a6,#8a6e55 60%,#d9d3cc)"></div>
  <h4>Lorem Ipsum header</h4><div class="mini"></div>
  <p>Lorem ipsum dolor sit amet, consectetur adipiscing elit, sed do eiusmod tempor incididunt dolore magna aliqua</p>
  <div class="read">Read More<svg width="28" height="28"><circle cx="14" cy="14" r="13" fill="#fff"/><path d="M8 14 H20 M16 10 L20 14 L16 18" fill="none" stroke="#6b8cf5" stroke-width="1.5"/></svg></div>
</article>
<article class="post" style="left:444px">
  <div class="accent"></div><div class="accent2"></div>
  <div class="photo" role="img" aria-label="Person wearing a virtual reality headset" style="background:linear-gradient(135deg,#c8c0b0,#a9a08e 55%,#6e8aa6)"></div>
  <h4>Lorem Ipsum header</h4><div class="mini"></div>
  <p>Lorem ipsum dolor sit amet, consectetur adipiscing elit, sed do eiusmod tempor incididunt dolore magna aliqua</p>
  <div class="read">Read More<svg width="28" height="28"><circle cx="14" cy="14" r="13" fill="#fff"/><path d="M8 14 H20 M16 10 L20 14 L16 18" fill="none" stroke="#6b8cf5" stroke-width="1.5"/></svg></div>
</article>
<article class="post" style="left:791px">
  <div class="accent"></div><div class="accent2"></div>
  <div class="photo" role="img" aria-label="Person working at a desk with several monitors" style="background:linear-gradient(135deg,#2b3330,#3f5a50 55%,#8fa7a0)"></div>
  <h4>Lorem Ipsum header</h4><div class="mini"></div>
  <p>Lorem ipsum dolor sit amet, consectetur adipiscing elit, sed do eiusmod tempor incididunt dolore magna aliqua</p>
  <div class="read">Read More<svg width="28" height="28"><circle cx="14" cy="14" r="13" fill="#fff"/><path d="M8 14 H20 M16 10 L20 14 L16 18" fill="none" stroke="#6b8cf5" stroke-width="1.5"/></svg></div>
</article>

<section class="cta" role="img" aria-label="Team working together around a table with laptops and tablets, darkened">
  <div class="tag">Want to work with us?</div>
  <h2>Lorem ipsum dolor sit amet !</h2>
  <p>Lorem ipsum dolor sit amet, consectetur adipiscing elit, sed do eiusmod tempor incididunt ut labore et dolore magna aliqua. Ut enim ad minim veniam, quis nostrud consectetur vo-luptatem accusantium doloremque adipiscing elit</p>
  <div class="btn-grad">Contact Us</div>
</section>

<footer class="footer">
  <h5 style="left:99px">About Us</h5><div class="mini" style="left:99px"></div>
  <p class="about">Lorem ipsum dolor sit amet, consectetur adip-iscing elit. Integer sit amet turpis venenatis nulla dignissim scelerisque. Ut volutpat maxi-mus ligula.</p>
  <h5 style="left:443px">Main Links</h5><div class="mini" style="left:443px"></div>
  <ul class="links"><li>Home</li><li>About Us</li><li>Our Products</li><li>Our Team</li><li>Case Study</li><li>Contact Us</li></ul>
  <h5 style="left:751px">Contact Us</h5><div class="mini" style="left:751px"></div>
  <div class="contact">
    <div><svg width="12" height="15"><path d="M6 0 A6 6 0 0 1 12 6 C12 10 6 15 6 15 C6 15 0 10 0 6 A6 6 0 0 1 6 0Z" fill="#8a7ff2"/><circle cx="6" cy="6" r="2" fill="#1e1d42"/></svg><b>Address:</b>48 Lantern Row Ashby, TX 40218</div>
    <div><svg width="13" height="13"><path d="M3 0 L5 4 L3.5 5.5 C4.5 8 6 9.5 7.5 10.5 L9 9 L13 11 L11 13 C5 12 1 8 0 2Z" fill="#8a7ff2"/></svg><b>Phone:</b>1-800-555-01-42</div>
    <div><svg width="15" height="11"><rect width="15" height="11" fill="#8a7ff2"/><path d="M0 0 L7.5 6 L15 0" fill="none" stroke="#1e1d42" stroke-width="1.2"/></svg><b>Mail:</b>hello@pellowar.dev</div>
  </div>
</footer>

<div class="base">
  <div class="brand"><span class="brand-dot"></span>Pellowar</div>
  <div class="copy">COPYRIGHT © 2022 PELLOWAR</div>
  <div class="social"><span></span><span></span><span></span><span></span></div>
</div>

</body>
</html>
```